New Fun, Positive, energised looking Business Card Needed for High Achiever Coach

I am looking for a two sided full colour business card. I am self employed and have recently re branded my 1-2-1 work re-vitalising high achievers. My target client base for these cards is therefore high achievers - usually aged 40 -55, they are often entrepreneurs, CEO or work in banking and finance and 2/3 are male. I work with them on 90 day or 6 month coaching programs to help them live their success in a healthier, more sustainable and fulfiiled way. They pay for this privately so though they are corporate types the cards need not look 'corporate'. I want to portray the idea of transformation, vitality and re-connecting.
You can get a feel for the look I like on my new website: morvenlisk.co.uk
I want to use this logo with strapline (Re-Vitalising High Achievers) (I purchased off Logoharbor) and font/ colours (the turquoise and green).
Details to include on the card:
www.morvenlisk.co.uk
+44 7915 302618
morven@morvenlisk.co.uk
skype: morvenlisk
I'd also like to include:
Do you struggle to switch off? Want to be healthier and feel fitter? Want closer relationships? More clarity over the direction you are headed? I can help you do these things using integrated mind-body techniques. Visit morvenlisk.co.uk TODAY to apply for a FREE Breakthrough session.
BUT if that is too much text for a card I am open to advice/ammendments.
Updates
Thanks for your design - I am considering them. PLease change the wording to :

```html
<!DOCTYPE html>
<html lang="en">
<head>
<meta charset="utf-8">
<title>Morven Lisk — Business Card</title>
<link href="https://fonts.googleapis.com/css2?family=Open+Sans:wght@400;700&display=swap" rel="stylesheet">
<style>
  :root {
    --teal: #0aa3c6;
    --green: #5cb85f;
    --ink: #3a3a3a;
    --paper: #ffffff;
    --backdrop: #e9eaf0;
    --rule: #cfcfcf;
  }
  * { box-sizing: border-box; margin: 0; padding: 0; }
  html, body {
    width: 1200px; height: 987px; overflow: hidden;
    background: var(--backdrop);
    font-family: "Open Sans", sans-serif;
    color: var(--ink);
  }
  .stage {
    position: relative; width: 1200px; height: 987px;
  }
  .card {
    position: absolute; left: 250px;
    width: 700px; height: 400px;
    background: var(--paper);
    border-radius: 34px;
    overflow: hidden;
    box-shadow: 0 6px 20px rgba(0,0,0,0.12);
  }
  .card--back { top: 60px; }
  .card--front { top: 527px; }

  .brand {
    position: absolute; left: 60px; top: 120px; width: 240px;
    display: flex; align-items: center; gap: 12px;
  }
  .card--front .brand { top: 90px; }
  .brand__dot {
    width: 26px; height: 26px; border-radius: 50%;
    background: var(--green); flex: none;
  }
  .brand__name {
    font-weight: 700; font-size: 34px; color: var(--teal);
    letter-spacing: 0.5px; white-space: nowrap;
  }

  .divider {
    position: absolute; left: 330px; width: 1px;
    background: var(--rule);
  }
  .card--back .divider { top: 60px; height: 260px; }
  .card--front .divider { top: 60px; height: 150px; }

  .pitch {
    position: absolute; left: 360px; top: 62px; width: 320px;
    font-size: 17px; line-height: 1.35;
  }
  .pitch p + p { margin-top: 12px; }
  .pitch strong { font-weight: 700; }

  .contacts {
    position: absolute; left: 360px; top: 70px;
    list-style: none; font-size: 22px;
  }
  .contacts li {
    display: flex; align-items: center; gap: 12px; margin-bottom: 10px;
  }
  .contacts svg { width: 22px; height: 22px; flex: none; }

  .wave {
    position: absolute; left: 0; top: 0; width: 700px; height: 400px;
  }
  .site {
    position: absolute; left: 40px; top: 312px;
    font-size: 24px; letter-spacing: 2px; color: var(--paper);
    transform: rotate(12deg); transform-origin: left center;
  }
</style>
</head>
<body>
<main class="stage">

  <section class="card card--back" aria-label="Card back">
    <div class="brand">
      <span class="brand__dot"></span>
      <span class="brand__name">Morven Lisk</span>
    </div>
    <span class="divider"></span>
    <div class="pitch">
      <p>Do you struggle to switch off?<br>
      Want to be healthier and feel fitter?<br>
      Want closer relationships?<br>
      More clarity over the direction you are headed?</p>
      <p>I can help you do these things using integrated mind-body techniques.</p>
      <p>Visit <strong>morvenlisk.co.uk</strong> TODAY to apply for a FREE Breakthrough session.</p>
    </div>
  </section>

  <section class="card card--front" aria-label="Card front">
    <svg class="wave" viewBox="0 0 700 400" aria-hidden="true">
      <path d="M0 230 C 180 230, 280 300, 400 345 S 620 400, 700 392 L700 400 L0 400 Z" fill="var(--teal)"/>
      <path d="M0 220 C 180 218, 290 290, 410 332 S 620 390, 700 380" fill="none" stroke="var(--green)" stroke-width="3"/>
    </svg>
    <div class="brand">
      <span class="brand__dot"></span>
      <span class="brand__name">Morven Lisk</span>
    </div>
    <span class="divider"></span>
    <ul class="contacts">
      <li>
        <svg viewBox="0 0 24 24" aria-hidden="true"><circle cx="12" cy="12" r="11" fill="none" stroke="var(--teal)" stroke-width="2"/><path d="M8 7c0 5 4 9 9 9l1-2-3-1-1 1c-2-1-3-2-4-4l1-1-1-3z" fill="var(--teal)"/></svg>
        <span>+44 7915 302618</span>
      </li>
      <li>
        <svg viewBox="0 0 24 24" aria-hidden="true"><rect x="2" y="5" width="20" height="14" rx="2" fill="var(--teal)"/><path d="M3 6l9 7 9-7" fill="none" stroke="#fff" stroke-width="2"/></svg>
        <span>morven@morvenlisk.co.uk</span>
      </li>
      <li>
        <svg viewBox="0 0 24 24" aria-hidden="true"><circle cx="12" cy="12" r="10" fill="var(--teal)"/></svg>
        <span>morvenlisk</span>
      </li>
    </ul>
    <span class="site">www.morvenlisk.co.uk</span>
  </section>

</main>
</body>
</html>
```